Brindle Recycling needs a new web design

We need a new web design for our company based in Austin, TX. We resell and recycling electronics such as laptops, computer components, Zelvotabs, Quorns, etc. Since our inception over ten years ago, we’ve become one of the premier electronics recycling and remarketing companies in Austin, Texas.

```html
<!DOCTYPE html>
<html lang="en">
<head>
<meta charset="utf-8">
<title>Brindle Recycling</title>
<link href="https://fonts.googleapis.com/css2?family=Lora:wght@400;700&family=Roboto:wght@400;500;700&display=swap" rel="stylesheet">
<style>
:root{
  --blue:#1c5dae;
  --blue-dark:#154a8f;
  --ink:#222;
  --muted:#666;
  --panel-dark:#2b2b2b;
  --footer:#1d1d1d;
  --footer-deep:#121212;
  --white:#fff;
}
*{margin:0;padding:0;box-sizing:border-box}
html,body{width:1200px;height:3913px;overflow:hidden}
body{position:relative;background:var(--white);font-family:"Roboto",sans-serif;color:var(--ink)}
.abs{position:absolute}
.serif{font-family:"Lora",serif}

/* header */
.site-header{left:0;top:0;width:1200px;height:76px;background:var(--white);z-index:5}
.brand{left:100px;top:14px;display:flex;align-items:center;gap:12px}
.brand-dot{width:46px;height:46px;border-radius:50%;background:var(--blue)}
.brand-name{font-family:"Lora",serif;font-weight:700;font-size:26px;color:var(--blue)}
.main-nav{right:100px;top:28px;display:flex;gap:52px;font-size:15px;font-weight:500;color:var(--ink)}

/* hero */
.hero{left:0;top:76px;width:1200px;height:580px;
  background:linear-gradient(180deg,#8fb1d9 0%,#c7d8ec 45%,#e8eef6 100%);
  clip-path:polygon(0 0,100% 0,100% 550px,50% 580px,0 550px)}
.hero-object{left:640px;top:110px;width:520px;height:500px;
  background:radial-gradient(ellipse at 55% 60%,#1f4fa8 0%,#2f62b8 40%,rgba(190,190,190,.6) 70%,rgba(220,225,235,0) 100%)}
.hero-kicker{left:98px;top:248px;font-family:"Lora",serif;font-weight:700;font-size:28px;color:var(--white);letter-spacing:1px}
.hero-title{left:96px;top:296px;font-weight:700;font-size:68px;line-height:82px;color:var(--white)}
.scroll-cue{left:588px;top:670px}

/* buttons */
.btn{display:flex;align-items:center;justify-content:center;gap:10px;background:var(--blue);color:var(--white);
  font-size:16px;font-weight:500;height:48px;
  clip-path:polygon(0 0,88% 0,100% 50%,88% 100%,0 100%,5% 50%)}
.btn-outline{display:flex;align-items:center;justify-content:center;gap:10px;color:var(--white);font-size:15px;height:42px;width:190px}

/* welcome */
.welcome-photo{left:115px;top:822px;width:456px;height:352px;background:linear-gradient(135deg,#6a4a3c,#3d6a3a 55%,#2e5d36);}
.welcome-shadow{left:96px;top:835px;width:475px;height:352px;background:#e6e6e6}
.welcome-title{left:634px;top:812px;font-family:"Lora",serif;font-size:46px;line-height:58px;color:var(--ink)}
.welcome-text{left:634px;top:968px;width:470px;font-size:14px;line-height:30px;color:var(--muted)}

/* section titles */
.section-title{left:0;width:1200px;text-align:center;font-family:"Lora",serif;font-size:46px;color:var(--ink)}
.rule{left:576px;width:48px;height:3px;background:var(--blue)}
.section-sub{left:300px;width:600px;text-align:center;font-size:14px;line-height:29px;color:var(--ink)}

/* services */
.services-band{left:0;top:1420px}
.service{width:600px;text-align:center;color:var(--white)}
.service h3{font-family:"Lora",serif;font-weight:400;font-size:25px}
.service .tag{font-family:"Lora",serif;font-style:italic;font-size:15px;margin-top:6px}
.service p{width:470px;margin:22px auto 0;font-size:13.5px;line-height:28px}
.service .btn-outline{margin:28px auto 0}

/* company */
.company-text{left:240px;top:2064px;width:720px;text-align:center;font-size:14px;line-height:32px;color:var(--muted)}

/* contact */
.contact-band{left:0;top:2374px;width:1200px;height:653px;background:linear-gradient(160deg,#2d6cc0 0%,#1c5dae 50%,#14488c 100%)}
.contact-title{left:0;top:2466px;width:1200px;text-align:center;font-family:"Lora",serif;font-size:46px;color:var(--white)}
.contact-intro{left:250px;top:2552px;width:700px;text-align:center;font-size:14px;line-height:30px;color:var(--white)}
.field{background:var(--white);font-size:13px;color:#444;padding:14px 16px;height:44px}
.send{left:545px;top:2882px;width:110px;height:36px;border:1px solid var(--white);border-radius:18px;color:var(--white);font-size:14px;display:flex;align-items:center;justify-content:center;gap:8px}

/* map */
.map{left:0;top:3027px;width:1200px;height:482px;background:linear-gradient(135deg,#e4e2dc,#d8dcd6 50%,#e6e3dd)}
.map-card{left:486px;top:3146px;width:228px;height:58px;background:var(--white);font-size:13px;line-height:20px;padding:9px 16px;color:#333;box-shadow:0 1px 4px rgba(0,0,0,.25)}

/* info strip */
.info-strip{left:0;top:3509px;width:1200px;height:138px;background:var(--footer)}
.info-item{display:flex;align-items:center;gap:22px;color:var(--white);font-family:"Lora",serif;font-size:13px;line-height:22px}
.info-icon{width:52px;height:52px;border-radius:50%;background:var(--blue);display:flex;align-items:center;justify-content:center;flex:none}

/* footer */
.site-footer{left:0;top:3647px;width:1200px;height:266px;background:var(--footer-deep)}
.footer-nav{left:258px;top:3693px;display:flex;gap:42px;font-family:"Lora",serif;font-size:14px;color:var(--white)}
.social{top:3684px;width:40px;height:40px;border:1px solid var(--white);border-radius:50%}
.cert-title{left:0;top:3756px;width:1200px;text-align:center;font-family:"Lora",serif;font-weight:700;font-size:16px;color:var(--white)}
.badge{top:3792px;width:46px;height:46px;border-radius:50%}
.copyright{left:0;top:3864px;width:1200px;text-align:center;font-size:11px;color:#bbb}
</style>
</head>
<body>

<header class="site-header abs">
  <div class="brand abs"><span class="brand-dot"></span><span class="brand-name">Brindle Recycling</span></div>
  <nav class="main-nav abs">
    <span>Home</span><span>About Us</span><span>Page</span><span>Support</span><span>Services</span><span>Contact Us</span>
    <svg width="16" height="16" viewBox="0 0 16 16"><circle cx="6.5" cy="6.5" r="4.5" fill="none" stroke="#222" stroke-width="2"/><line x1="10" y1="10" x2="14" y2="14" stroke="#222" stroke-width="2"/></svg>
  </nav>
</header>

<section class="hero abs" role="img" aria-label="Cloudy sky with a blue recycling bin full of old computer equipment"></section>
<div class="hero-object abs" role="img" aria-label="Recycling bin loaded with monitors, keyboards and computer parts"></div>
<p class="hero-kicker abs">BRINDLE RECYCLING</p>
<h1 class="hero-title abs">Recycling Today<br>Reuse Tomorrow</h1>
<a class="btn abs" style="left:99px;top:482px;width:202px">Learn More <span>»</span></a>
<svg class="scroll-cue abs" width="24" height="28" viewBox="0 0 24 28"><path d="M4 4l8 8 8-8M4 14l8 8 8-8" fill="none" stroke="#9aa" stroke-width="2"/></svg>

<div class="welcome-shadow abs"></div>
<div class="welcome-photo abs" role="img" aria-label="People dropping electronic items into a green recycling bin"></div>
<h2 class="welcome-title abs">Welcome To<br>Brindle Recycling</h2>
<p class="welcome-text abs">At Brindle Recycling, we're committed to providing environmentally friendly recycling solutions to Austin and the surrounding areas. Founded in 2006, our mission is to process your materials in a safe, non-hazardous manner — with an aim to keep the world environmentally clean.</p>
<a class="btn abs" style="left:634px;top:1140px;width:168px">Read More <span>»</span></a>

<h2 class="section-title abs" style="top:1280px">Recycling Services</h2>
<div class="rule abs" style="top:1358px"></div>
<p class="section-sub abs" style="top:1376px">Sed ut perspiciatis unde omnis iste natus error sit voluptatem accusantium doloremque laudantium, totam rem aperiam</p>

<svg class="services-band abs" width="1200" height="460" viewBox="0 0 1200 460" role="img" aria-label="Photos of electronic waste with dark and blue overlays">
  <defs>
    <linearGradient id="darkPanel" x1="0" y1="0" x2="1" y2="1"><stop offset="0" stop-color="#3a3a3a"/><stop offset="1" stop-color="#1f1f1f"/></linearGradient>
    <linearGradient id="bluePanel" x1="0" y1="0" x2="1" y2="1"><stop offset="0" stop-color="#2766b8"/><stop offset="1" stop-color="#16498f"/></linearGradient>
  </defs>
  <polygon points="0,10 600,67 600,458 0,400" fill="url(#darkPanel)"/>
  <polygon points="600,67 1200,10 1200,400 600,458" fill="url(#bluePanel)"/>
</svg>
<div class="service abs" style="left:0;top:1528px">
  <h3>Electronic Recycling</h3>
  <p class="tag">Environmentally Friendly</p>
  <p>At Brindle Recycling, we strive to keep the environment clean through our wide range of services. Our E-Waste Recycling services were designed to simplify the recycling process for residents in the Austin area. Contact us today and see how you can contribute to making this world a cleaner place.</p>
  <div class="btn-outline"><svg class="abs" width="190" height="42" viewBox="0 0 190 42"><polygon points="1,1 170,1 189,21 170,41 1,41 12,21" fill="none" stroke="#fff"/></svg>Schedule a pickup »</div>
</div>
<div class="service abs" style="left:600px;top:1528px">
  <h3>Recycling Pickup</h3>
  <p class="tag">We Come To You</p>
  <p>At Brindle Recycling, we go out of our way to make sure your recycling process is made easy as possible. Our Recycling Pickup service is designed to simplify all of your recycling needs. Take a look at all the services we offer and get in touch to see how you can start the process today!</p>
  <div class="btn-outline"><svg class="abs" width="190" height="42" viewBox="0 0 190 42"><polygon points="1,1 170,1 189,21 170,41 1,41 12,21" fill="none" stroke="#fff"/></svg>Schedule a pickup »</div>
</div>

<h2 class="section-title abs" style="top:1972px">Our Company</h2>
<p class="company-text abs">What most people do not realize is electronic waste represents 2% of America's trash in landfills, but it equals 70% of overall toxic waste. Used computer equipment is a rapidly growing source of waste across the country. Only 12.5% of electronic waste is currently recycled in the US. Computers contain valuable parts that we can recycle, and heavy metals that we should try to keep out of landfills. Despite this, Texas has historically had low computer recycling rates in the past.</p>
<a class="btn abs" style="left:529px;top:2226px;width:142px">Read More <span>»</span></a>

<section class="contact-band abs" role="img" aria-label="Aerial view of a city with a blue overlay"></section>
<h2 class="contact-title abs">Contact Us</h2>
<p class="contact-intro abs">Interested in helping to make the world a greener place? Get in touch with Brindle Recycling, and learn more about the wide range of recycling services and facilities that are at your disposal.</p>
<div class="field abs" style="left:172px;top:2646px;width:420px">Name</div>
<div class="field abs" style="left:608px;top:2646px;width:420px">Phone No</div>
<div class="field abs" style="left:172px;top:2712px;width:420px">Email Address</div>
<div class="field abs" style="left:608px;top:2712px;width:420px">Address</div>
<div class="field abs" style="left:172px;top:2776px;width:420px;height:82px">Subject</div>
<div class="field abs" style="left:608px;top:2776px;width:420px;height:82px">Message</div>
<div class="send abs"><svg width="14" height="14" viewBox="0 0 14 14"><path d="M1 6l12-5-5 12-1.5-5z" fill="#fff"/></svg>Send</div>

<div class="map abs" role="img" aria-label="Street map of Austin, Texas, with a pin at the office location"></div>
<div class="map-card abs">2215 Cedar Bend Dr<br>Austin, Texas 78757</div>
<svg class="abs" style="left:538px;top:3204px" width="22" height="30" viewBox="0 0 22 30"><path d="M11 29C11 29 2 17 2 11a9 9 0 0 1 18 0c0 6-9 18-9 18z" fill="#d93a2b"/><circle cx="11" cy="11" r="3.5" fill="#8a1f16"/></svg>

<section class="info-strip abs"></section>
<div class="info-item abs" style="left:168px;top:3550px">
  <span class="info-icon"><svg width="16" height="22" viewBox="0 0 16 22"><path d="M8 21S1 12 1 8a7 7 0 0 1 14 0c0 4-7 13-7 13z" fill="#fff"/><circle cx="8" cy="8" r="2.5" fill="#1c5dae"/></svg></span>
  <span>2215 Cedar Bend Dr<br>Austin TX USA 78757</span>
</div>
<div class="info-item abs" style="left:494px;top:3550px">
  <span class="info-icon"><svg width="20" height="20" viewBox="0 0 20 20"><path d="M4 1l4 4-2 3c1 2 4 5 6 6l3-2 4 4-3 3C8 19 1 12 1 4z" fill="#fff"/></svg></span>
  <span>(512)555-0147</span>
</div>
<div class="info-item abs" style="left:812px;top:3550px">
  <span class="info-icon"><svg width="20" height="20" viewBox="0 0 20 20"><path d="M1 9L19 1l-6 18-3-7z" fill="#fff"/></svg></span>
  <span>dana@brindlerecycling.com</span>
</div>

<footer class="site-footer abs"></footer>
<nav class="footer-nav abs"><span>Home</span><span>About Us</span><span>Page</span><span>Support</span><span>Services</span><span>Contact Us</span></nav>
<span class="social abs" style="left:798px"></span>
<span class="social abs" style="left:850px"></span>
<span class="social abs" style="left:902px"></span>
<p class="cert-title abs">Certificate of Certification</p>
<span class="badge abs" style="left:376px;background:#b8c4d8"></span>
<span class="badge abs" style="left:468px;background:#2a5db0"></span>
<span class="badge abs" style="left:578px;background:#3d9a3d"></span>
<span class="badge abs" style="left:690px;background:#6f8a6f"></span>
<span class="badge abs" style="left:780px;background:#8a8a8a"></span>
<p class="copyright abs">© 2018 Copyrights Brindlerecycling All Rights Reserved</p>

</body>
</html>
```